New Innovative Counselling and psychotherapy Service needs Business Card design

Keep it simple and professional. On one side, just company name and logo (perhaps in all blue) and maybe a tag line.

On other side (all white) my name and Qualifications in centre

Industry/Entity Type

Health And Wellness

Contact Information for Business Card

Dara Whelby
Counsellor & Psychotherapist
BSc (Psychol.), BA, Dip. (Couns. & Psych.), PG.Cert (CBT), FGTrK, ONRE

I will also require Mobile no, Email and web site address of which I'll pass on to final designer.

Font styles to use
Sans Serif

Requirements
Must have
• My Logo Only and please use the colours in logo that is in it.
Should not have
• Any other images

```html
<!DOCTYPE html>
<html lang="en">
<head>
<meta charset="utf-8">
<title>Kindred Lane – Business Card</title>
<link rel="stylesheet" href="https://fonts.googleapis.com/css2?family=Raleway:wght@300;400&family=Open+Sans:wght@400;600;700&display=swap">
<style>
  :root {
    --stage: #2b2d30;
    --sky-light: #63d6f8;
    --sky: #3fb0ec;
    --sky-deep: #3aa6ea;
    --leaf: #8ccf4d;
    --ink: #3b3d40;
    --paper: #f7f7f7;
    --tagline: #4c6f86;
  }
  * { box-sizing: border-box; margin: 0; padding: 0; }
  html, body { width: 1200px; height: 900px; overflow: hidden; }
  body {
    background: var(--stage);
    font-family: "Open Sans", Arial, sans-serif;
    display: flex;
    flex-direction: column;
    align-items: center;
    justify-content: center;
    gap: 48px;
  }
  .card {
    width: 640px;
    height: 366px;
    position: relative;
    overflow: hidden;
    box-shadow: 0 14px 30px rgba(0,0,0,.45);
  }

  /* Front */
  .card--front {
    background: linear-gradient(100deg, var(--sky-light) 0%, var(--sky) 55%, var(--sky-deep) 100%);
    display: flex;
    flex-direction: column;
    align-items: center;
  }
  .front__brand {
    margin-top: 120px;
    display: flex;
    align-items: center;
    gap: 16px;
    color: #ffffff;
    font-family: "Raleway", Arial, sans-serif;
    font-weight: 300;
    font-size: 46px;
    letter-spacing: .5px;
  }
  .brand-dot {
    width: 22px; height: 22px;
    border-radius: 50%;
    background: #ffffff;
    flex: none;
  }
  .front__tagline {
    position: absolute;
    bottom: 44px;
    width: 100%;
    text-align: center;
    color: var(--tagline);
    font-size: 15px;
    letter-spacing: .2px;
  }

  /* Back */
  .card--back {
    background: var(--paper);
    display: flex;
    flex-direction: column;
    align-items: center;
  }
  .back__brand {
    margin-top: 46px;
    display: flex;
    align-items: center;
    gap: 16px;
    color: var(--ink);
    font-family: "Raleway", Arial, sans-serif;
    font-weight: 300;
    font-size: 38px;
  }
  .back__brand .brand-dot { width: 40px; height: 40px; background: var(--sky-deep); }
  .person {
    margin-top: 30px;
    text-align: center;
  }
  .person__name {
    color: var(--sky-deep);
    font-weight: 700;
    font-size: 19px;
    text-transform: uppercase;
    letter-spacing: .3px;
  }
  .person__role {
    color: var(--leaf);
    font-size: 16px;
    text-transform: uppercase;
    letter-spacing: .3px;
    margin-top: 2px;
  }
  .person__quals {
    color: var(--leaf);
    font-size: 12px;
    line-height: 1.45;
    margin-top: 3px;
  }
  .contact {
    margin-top: 14px;
    text-align: center;
    color: var(--ink);
    font-size: 15px;
    line-height: 1.45;
  }
  .contact__label { color: var(--sky-deep); font-weight: 700; }
  .contact__item + .contact__item { margin-left: 6px; }
  .back__stripe {
    position: absolute;
    left: 0; right: 0; bottom: 0;
    height: 10px;
    display: flex;
  }
  .back__stripe-blue { flex: 4; background: var(--sky-deep); }
  .back__stripe-green { flex: 1; background: var(--leaf); margin-left: 4px; }
</style>
</head>
<body>

  <section class="card card--front" aria-label="Card front">
    <div class="front__brand"><span class="brand-dot"></span>Kindred Lane</div>
    <p class="front__tagline">Caring For Your Psychological Well-Being Is Our Top Priority</p>
  </section>

  <section class="card card--back" aria-label="Card back">
    <div class="back__brand"><span class="brand-dot"></span>Kindred Lane</div>

    <div class="person">
      <h1 class="person__name">Dara Whelby</h1>
      <p class="person__role">Counsellor &amp; Psychotherapist</p>
      <p class="person__quals">BSc (Psychol.), BA, Dip. (Couns. &amp; Psych.)<br>PG.Cert (CBT), FGTrK,</p>
    </div>

    <div class="contact">
      <p>
        <span class="contact__item"><span class="contact__label">P:</span> 555 210 4871</span>
        <span class="contact__item"><span class="contact__label">E:</span> dara@kindredlane.com</span>
      </p>
      <p><span class="contact__label">W:</span> www.kindredlane.com</p>
    </div>

    <div class="back__stripe">
      <span class="back__stripe-blue"></span>
      <span class="back__stripe-green"></span>
    </div>
  </section>

</body>
</html>
```